Marlow Estate Fixers (Handyman / Home Improvement Company)

Looking for a double sided professional looking business card with Logo attached to be highlighted on one side and throwing in an image of a handyman as an option would be nice to see as well. We are a company focused on providing quality Handyman and Home improvement services in a timely manner that is done right the first time with integrity

Industry/Entity Type

Handyman / Home Improvement

Contact Information for Business Card

(LOGO, Name, Mobile and office phone numbers, email) on front side of card, (the words "The SOLUTION to all of your Handyman and Home Improvement needs" followed by "Family Owned and Operated" at the very bottom) on the back.

Colors
EB3D1F
EC4F4E
F09395
F8D3D4
FCEDEE

Requirements
Must have
• Red, Gray, Black Color scheme
Should not have
• No Yellow or Blue colors

```html
<!DOCTYPE html>
<html lang="en">
<head>
<meta charset="UTF-8">
<title>Marlow Estate Fixers – Business Card</title>
<link href="https://fonts.googleapis.com/css2?family=Montserrat:wght@400;500;800&display=swap" rel="stylesheet">
<style>
  :root {
    --bg: #3a3a3a;
    --card-dark: #0b0b0b;
    --card-light: #ffffff;
    --red: #eb3d1f;
    --ink: #111111;
    --ink-muted: #333333;
    --white: #ffffff;
  }
  * { box-sizing: border-box; margin: 0; padding: 0; }
  html, body {
    width: 1200px; height: 875px; overflow: hidden;
    background: var(--bg);
    font-family: "Montserrat", sans-serif;
  }
  .stage {
    width: 1200px; height: 875px;
    display: flex; align-items: center; justify-content: center; gap: 40px;
  }
  .card {
    width: 520px; height: 297px;
    border-radius: 18px;
    position: relative;
    overflow: hidden;
    box-shadow: 0 12px 30px rgba(0,0,0,.35);
  }

  /* Back side */
  .card--back {
    background: var(--card-dark);
    display: flex; align-items: center; justify-content: center;
  }
  .brand {
    display: flex; align-items: center; gap: 12px;
    font-weight: 800; text-transform: uppercase; letter-spacing: .04em;
    white-space: nowrap;
  }
  .brand__dot {
    border-radius: 50%;
    background: var(--red);
    flex: none;
  }
  .card--back .brand { color: var(--white); font-size: 26px; }
  .card--back .brand__dot { width: 26px; height: 26px; }

  /* Front side */
  .card--front { background: var(--card-light); color: var(--ink); }
  .card--front .brand {
    position: absolute; top: 58px; right: 30px;
    color: var(--red); font-size: 17px;
  }
  .card--front .brand__dot { width: 18px; height: 18px; }

  .person {
    position: absolute; left: 30px; top: 146px;
  }
  .person__name { font-size: 22px; font-weight: 800; line-height: 1.1; }
  .person__name .surname { color: var(--red); }
  .person__role { font-size: 12px; font-weight: 500; color: var(--ink-muted); margin-top: 3px; }

  .divider {
    position: absolute; left: 30px; right: 30px; top: 196px;
    height: 1px; background: var(--red);
  }

  .contacts {
    position: absolute; left: 30px; top: 208px;
    list-style: none; font-size: 11.5px; font-weight: 500; color: var(--ink);
  }
  .contacts li { display: flex; align-items: center; gap: 9px; line-height: 20px; white-space: nowrap; }
  .contacts svg { width: 12px; height: 12px; fill: var(--red); flex: none; }

  .address {
    position: absolute; right: 30px; top: 212px;
    font-style: normal;
    font-size: 11.5px; font-weight: 500; text-align: right; line-height: 1.45;
    color: var(--ink);
  }
</style>
</head>
<body>
<main class="stage">
  <section class="card card--back" aria-label="Business card back">
    <div class="brand"><span class="brand__dot"></span>Marlow Estate Fixers</div>
  </section>

  <section class="card card--front" aria-label="Business card front">
    <div class="brand"><span class="brand__dot"></span>Marlow Estate Fixers</div>

    <div class="person">
      <p class="person__name">Owen <span class="surname">Harlow</span></p>
      <p class="person__role">Managing Director</p>
    </div>

    <div class="divider"></div>

    <ul class="contacts">
      <li>
        <svg viewBox="0 0 24 24" aria-hidden="true"><path d="M6.6 10.8a15.1 15.1 0 0 0 6.6 6.6l2.2-2.2a1 1 0 0 1 1-.25 11.4 11.4 0 0 0 3.6.57 1 1 0 0 1 1 1V20a1 1 0 0 1-1 1A17 17 0 0 1 3 4a1 1 0 0 1 1-1h3.5a1 1 0 0 1 1 1c0 1.25.2 2.45.57 3.6a1 1 0 0 1-.25 1z"/></svg>
        (08) 4410 2236
      </li>
      <li>
        <svg viewBox="0 0 24 24" aria-hidden="true"><path d="M2 5h20v14H2z M4 7v.5l8 5 8-5V7l-8 5z" fill-rule="evenodd"/></svg>
        hello@marlowfixers.com
      </li>
      <li>
        <svg viewBox="0 0 24 24" aria-hidden="true"><path d="M12 2a10 10 0 1 0 0 20 10 10 0 0 0 0-20zm0 2c.9 0 2.2 2 2.7 5H9.3C9.8 6 11.1 4 12 4zM4.3 11h3c0 .7 0 1.3.1 2h-3a8 8 0 0 1-.1-2zm.6 4h2.8c.3 1.4.8 2.6 1.4 3.5A8 8 0 0 1 4.9 15zm4.4 0h5.4c-.5 3-1.8 5-2.7 5s-2.2-2-2.7-5zm7 0h2.8a8 8 0 0 1-4.2 3.5c.6-.9 1.1-2.1 1.4-3.5zm.3-2c.1-.7.1-1.3.1-2h3a8 8 0 0 1-.1 2zM9.3 11h5.4a13 13 0 0 1 0 2H9.3a13 13 0 0 1 0-2z"/></svg>
        www.marlowfixers.com
      </li>
    </ul>

    <address class="address">48 Elm Road,<br>Riverton, USA</address>
  </section>
</main>
</body>
</html>
```